Talvoro Web Design

We need a redesign of our current website www.talvoro-example.com

THIS IS A DESIGN STAGE ONLY

We have attached details of the whole project for your understanding only

We do not want to change our Logo but do want to have a more modern and intuitive feel to the site.

The first stage is the design but we are also looking for a coder to take the site to the next level

Talvoro has a current website that has been in operation for the past 6 years the design was based around the Saas self-service model and while functional does not meet Talvoro needs with regard to the new positioning.

We are happy to stay in Joomla or will look at alternatives

The purpose of the redesign is to align the look and feel of the website to meet our current new brand position and to provide a access point for the delivery of new content from Blogs and white papers as well as a portal for information for our current users for gathering Tips and Tricks and access to additional resources to assist them to provide feedback and get support.

Talvoro is Australia's only PPM (Project and Portfolio Management) software provider that caters to the needs of project managers and C-level executives looking for insights into the alignment of resources to business strategy and investment decisions.

As companies gain maturity in PPM there is a need for innovation and management of change beyond just implementation of tools this is why Talvoro has evolved from being a SaaS to becoming a SwS (Software with Service) provider.

Talvoro is recognized as the tool of choice amongst program and project managers that is able to provide the user with an intuitive reliable interface that is capable of evolving and maturing to meet and exceed client requirements.

We are able to provide people at the coalface with tools that enable them to manage resources, scope, time sheeting, issues, changes and risk with excellent reporting functionality.

For C-level executives we are able to provide Business Intelligence (BI) functionality and reporting by integrating the PPM data with other business management systems such as ERP and CRM to provide a insight beyond pure PPM reporting.

We are able to provide Project Management insights from years of experience working with our clients in developing solutions that are inline with the evolution that comes with change.

Please feel free to email me on marcus.hale@talvoro-example.com if you require any further details. A Site map and a wire frame is available.

Competitor sites include

www.plenvix-example.com
www.corbelo-example.com
www.quandrit-example.com
www.vestrel-example.com
Updates

Hi All 

We are getting some great designs coming in and really appreciate all of your efforts.

Some feedback to you all is that we have a preference for cleaner designs that take into account comprehension ability. So reverse type to us looks good but doesnt always get the cut through.

We have to remember that this is a marketing site first and foremost so what we are looking for is the ability to engage with our audience and get them to start to explore. That is upto us to provide great content and what we want from the design is the ability to be be able to engage with our Audience.

For your consideration please review this info from our marketing plan

There are 3 main communication groups inthe sales process.

Users-        These are the peoplewho will be at the coal face inputting the data and using the product on adaily basis. It is key to provide them with an easy to use and functional toolthat is able to provide them with the information they are looking for easily andintuitively. They have the capacity to say yes and can push the sale decisionup the chain. They equally have the power to say No and stop the sales processin its tracks. They will have a opinion who or what they feel is the best ofbreed and will try to influence the process.

Users are split into two groups.

Group1- They will be diploma if not degree qualifiedwill be a mix of Male and female with majority aged 18 to 35 they are at thecareer development stage of their life cycle normally on an income 45k to 70kper annum. We would position these people very strongly in the “What is in itfor me”.

Group2- PM who has used a variety of tools and systemsover the years they will be pre disposed to one or more systems and has morethan likely been exposed to MSP. Usually in the 30 to 50 year old age rangewith extensive on the job experience.

KeyInfluencers- These are the people who while notactually utilizing the software need to receive information in the form ofreports etc from the system. They normally don’t have the capacity to say yesbut they most certainly can say no. They will have come from a PM or IT roleand have a strong understanding of the PM processes. Influencers will be 30 to50 years of age they are at the family development stage with strong demandsfrom work and family predominantly male but not exclusively. They would bedegree qualified and possibly have completed or looking at additional studies. Therewill be an emphasis on getting the job done right. They are very time poor and hardto communicate with and engage. While being time poor they have an affinitywith and understand the greater good.

DecisionMakers- These are our key decision makers whilethey may not have direct input into the system or processes they are at the endof the day the people who approve the expenditure.

There is a huge demand for this person’stime with a multitude of people from internal employees and management,suppliers, customers, the community and potential suppliers. They are oftentravelling and going from one subject matter to another meeting after meeting.They will be at the stage where children are gaining some independents or leftthe home, career is stabilized and a clear path is formed. They are very directand deal in the facts and figures when it comes to decision making, they arenormally highly educated to the MBA or Doctorate level. They will be driven byoutcomes not the process of getting there.

 

A consistent theme across this group isthe following.

Psychographics

·Values time and considers ittheir single most limited resource.

·Excited about accepting andusing innovative ideas and products always wants to be at the fore front.

·Value adding has priority overprice

·Consistent web users: preferinternet over magazines and newspapers

Behavior

·They are leaders in productselection and respond to the opinions of the ‘Industry Experts’ when makingpurchase decisions.

·This group will look to theinternet to acquire the information

·Will make an informed decisionto purchase after due consideration.

·This group can be a powerfulsales force resulting from the referral network they build and use

Hope this helps

Hi All

Sorry for the delay we are in the final stages of decisions, so sorry we have had people away from the office who need to be involved in the process.

We will submit individual questions to those in the running and let all of the people who didnt get through this time as to why shortly.

We would like to thank you all for your efforts and submissions.

Regards

Marcus Hale 

Industry/Entity Type

Business Management

Requirements
Must have
• The scope of the website is to provide a modern functional website that is easy to navigate and provides a range of products and services to meet the needs of our potential clients and current users.

Two potential groups of viewers exist:
1. Potential Clients and users from the Project management community these would be split into 3 distinct groups. ( Please refer to Page 20 Talvoro marketing Plan)
a. Project Managers
b. Project Directors
c. Business Managers
2. Current Talvoro Users

The goal of website is to engage with the project management community reinforcing the Talvoro Brand as Software with Service the key ethos should be around the company being thought leaders and industry experts with a strong commitment to clients and the success of their Portfolio/Program Management Office

Maintaining a modern and user friendly site is of the highest importance in order to hold users attention and guide the viewer to information that will lead to a decision to pursue accreditation and association with the Talvoro Brand

We would like to guide potential clients to want to engage with us in assisting them to understand their current position in the P3M3 maturity model and to use us as a source for information and guidance.

Benefits for using the site should include:
• Information from a broad spectrum of Project Management professionals and recognized industry experts.
• Information on the Talvoro Product and Services
• Timely and up to date information that encourages readers to return to the site
• Call to action, and plans for potential users of Talvoro software.
• Demonstrate the benefits of accreditation and Call to action for current users to gain accreditation.
• Call to action for attending monthly webinars
• Ability to review past webinars, whitepapers etc.

```html
<!DOCTYPE html>
<html lang="en">
<head>
<meta charset="utf-8">
<title>Talvoro – Resources Management Software</title>
<link rel="stylesheet" href="https://fonts.googleapis.com/css2?family=Open+Sans:wght@400;600;700&display=swap">
<style>
:root{
  --orange:#f26a1b;
  --orange-dark:#d9560d;
  --charcoal:#2a2a2a;
  --black:#0d0d0d;
  --ink:#333;
  --muted:#888;
  --rule:#dcdcdc;
  --panel:#f3f3f3;
  --footer:#ececec;
  --white:#fff;
}
*{box-sizing:border-box;margin:0;padding:0}
html,body{width:876px;height:1200px;overflow:hidden}
body{font-family:"Open Sans",Arial,sans-serif;color:var(--ink);background:var(--white);font-size:11px;line-height:1.5}
.wrap{width:790px;margin:0 auto;position:relative}
a{color:inherit;text-decoration:none}

/* header */
.site-header{background:var(--charcoal);height:82px;border-bottom:3px solid var(--orange)}
.site-header .wrap{height:100%}
.brand{position:absolute;left:0;top:14px;display:flex;align-items:center;gap:8px;color:var(--white);font-size:26px;font-weight:700}
.brand-dot{width:14px;height:14px;border-radius:50%;background:var(--orange)}
.utility{position:absolute;right:0;top:6px;color:#bbb;font-size:9px}
.utility span{margin:0 4px}
.main-nav{position:absolute;right:0;bottom:10px;display:flex}
.main-nav a{color:var(--white);font-weight:600;font-size:13px;padding:6px 14px;border-left:1px solid #444}
.main-nav a:first-child{border-left:none}

/* hero */
.hero{background:var(--black);height:225px;position:relative}
.hero .wrap{height:100%}
.hero-copy{position:absolute;left:45px;top:40px;width:270px}
.hero-title{color:var(--white);font-size:24px;font-weight:400;line-height:1.1}
.hero-title strong{display:block;color:var(--orange);font-size:34px;font-weight:600}
.hero-copy p{color:#bbb;font-size:10px;margin:10px 0 14px}
.btn{display:inline-block;background:var(--orange);color:var(--white);font-size:9px;font-weight:700;padding:5px 12px;border-radius:2px}
.hero-art{position:absolute;right:30px;top:20px;width:400px;height:185px;border-radius:6px;background:radial-gradient(ellipse at center,#3a2212 0%,#160c06 60%,var(--black) 100%)}
.hero-arrow{position:absolute;top:96px;color:#777;font-size:22px}
.hero-arrow.prev{left:-22px}.hero-arrow.next{right:-22px}
.dots{position:absolute;bottom:10px;left:50%;transform:translateX(-50%);display:flex;gap:5px}
.dots i{width:6px;height:6px;border-radius:50%;background:#555}
.dots i.on{background:var(--orange)}

/* features */
.features{display:flex;gap:18px;margin-top:30px}
.feature{flex:1;height:140px;border:1px solid var(--rule);background:linear-gradient(#fff,#f2f2f2);padding:12px 14px;position:relative}
.feature h3{color:var(--orange);font-size:15px;font-weight:600;margin-bottom:6px}
.feature p{width:120px;color:var(--muted);font-size:9px;line-height:1.4}
.feature .more{position:absolute;left:14px;bottom:12px;font-size:8px;font-weight:700;color:#444}
.feature-art{position:absolute;right:12px;top:44px;width:110px;height:70px;border-radius:4px}
.art-orange{background:linear-gradient(135deg,#f7b37e,#e05a10)}
.art-blue{background:linear-gradient(135deg,#e8eef6,#8aa3c7)}
.art-gold{background:linear-gradient(135deg,#f6dc9a,#c98a1e)}

/* content */
.content{display:flex;gap:30px;margin-top:38px}
.main-col{flex:1}
.side-col{width:200px}
.section-title{font-size:19px;font-weight:400;color:#555;padding-bottom:6px;border-bottom:1px solid var(--rule);margin-bottom:10px}
.side-col .section-title{color:var(--orange)}
.about p{color:var(--muted);font-size:9.5px;margin-bottom:8px}
.news-item{margin-bottom:14px}
.news-item h4{font-size:11px;font-weight:600;color:#444}
.news-item p{color:var(--muted);font-size:9px}
.news-item time{color:var(--orange);font-size:8.5px}

.services{margin-top:24px}
.service-list{display:flex;gap:22px}
.service{flex:1;display:flex;gap:8px}
.service-icon{flex:none;width:34px;height:34px;border-radius:50%}
.service h4{color:var(--orange);font-size:12px;font-weight:600}
.service p{color:var(--muted);font-size:8.5px;line-height:1.4}
.service .more{font-size:8px;font-weight:700;color:#444;margin-top:6px;display:block}

/* footer */
.site-footer{position:absolute;top:960px;left:0;width:876px;height:240px;background:var(--footer);border-top:1px solid var(--rule)}
.footer-cols{display:flex;padding-top:22px}
.footer-col{width:110px}
.footer-col h5{font-size:12px;font-weight:600;color:#444;margin-bottom:8px}
.footer-col li{list-style:none;font-size:9px;color:var(--muted);line-height:1.8}
.newsletter{margin-left:auto;width:240px}
.newsletter h5{font-size:12px;font-weight:600;color:#444;margin-bottom:6px}
.newsletter p{font-size:9px;color:var(--muted);margin-bottom:8px}
.newsletter form{display:flex;gap:6px}
.newsletter .field{flex:1;height:22px;border:1px solid #ccc;background:var(--white)}
.newsletter .btn{padding:5px 10px}
.social{display:flex;gap:5px;justify-content:flex-end;margin-top:46px}
.social i{width:18px;height:18px;border-radius:50%;background:#555}
.copyright{position:absolute;bottom:0;left:0;width:100%;height:26px;background:#dedede;font-size:8.5px;color:var(--muted);line-height:26px}
</style>
</head>
<body>
<header class="site-header">
  <div class="wrap">
    <a class="brand" href="#"><span class="brand-dot"></span>Talvoro</a>
    <div class="utility"><span>Home</span>|<span>FAQ</span>|<span>Support &amp; Training</span>|<span>Login</span>|<span>Contact</span></div>
    <nav class="main-nav">
      <a href="#">Tour</a><a href="#">Features</a><a href="#">Pricing</a><a href="#">Sign Up</a><a href="#">Download</a><a href="#">About Us</a>
    </nav>
  </div>
</header>

<section class="hero">
  <div class="wrap">
    <span class="hero-arrow prev">&#8249;</span>
    <div class="hero-copy">
      <h1 class="hero-title">Resources Management <strong>Software</strong></h1>
      <p>Nunc tempus felis vitae urna. Vivamus porttitor, ju purus nisi eleifend libero, a tempus libero lorem ut feugiat felis. Morbi diam mauris viverra in gravida eu.</p>
      <a class="btn" href="#">READ MORE</a>
    </div>
    <div class="hero-art" role="img" aria-label="Orange line illustration of business and resource planning icons"></div>
    <span class="hero-arrow next">&#8250;</span>
    <div class="dots"><i class="on"></i><i></i><i></i><i></i></div>
  </div>
</section>

<main class="wrap">
  <section class="features">
    <article class="feature">
      <h3>Project Management</h3>
      <p>Duis tincidunt lectus quis dui viverra vestibulum. Suspendisse vulputate aliquam dui.</p>
      <div class="feature-art art-orange" role="img" aria-label="Orange growth chart illustration"></div>
      <a class="more" href="#">LEARN MORE &#9656;</a>
    </article>
    <article class="feature">
      <h3>Resources Managment</h3>
      <p>Duis tincidunt lectus quis dui viverra vestibulum. Suspendisse vulputate aliquam dui.</p>
      <div class="feature-art art-blue" role="img" aria-label="Pale blue pyramid illustration"></div>
      <a class="more" href="#">LEARN MORE &#9656;</a>
    </article>
    <article class="feature">
      <h3>Timesheets</h3>
      <p>Duis tincidunt lectus quis dui viverra vestibulum. Suspendisse vulputate aliquam dui.</p>
      <div class="feature-art art-gold" role="img" aria-label="Gold stacked coins and clock illustration"></div>
      <a class="more" href="#">LEARN MORE &#9656;</a>
    </article>
  </section>

  <div class="content">
    <div class="main-col">
      <section class="about">
        <h2 class="section-title">About Our Company</h2>
        <p>Nunc tempus felis vitae urna. Vivamus porttitor, justo sit amet viverra ultricies, purus nisi eleifend libero, a tempus libero lorem ut feugiat felis. Morbi diam mauris, viverra in, gravida eu, mattis in, ante. Morbi eget arcu. Morbi porta, libero id ullamcorper nonummy, nibh ligula pulvinar metus.</p>
        <p>Phasellus felis dolor, scelerisque a, tempus eget, lobortis id, libero. Donec scelerisque leo ac risus. Praesent sit amet est. In dictum, dolor eu dictum porttitor, enim felis viverra mi, eget luctus massa purus quis odio. Etiam nulla massa, pharetra facilisis, volutpat in, imperdiet sit amet, sem.</p>
      </section>
      <section class="services">
        <h2 class="section-title">Featured Services</h2>
        <div class="service-list">
          <div class="service">
            <div class="service-icon" style="background:linear-gradient(135deg,#c9d3de,#6d7f95)" role="img" aria-label="Team member icon"></div>
            <div><h4>Services Title</h4><p>Sed sed tellus ut lorem vestibulum gravida. Vivamus elementum ut felis sodales. Curabitur rutrum.</p><a class="more" href="#">LEARN MORE &#9656;</a></div>
          </div>
          <div class="service">
            <div class="service-icon" style="background:linear-gradient(135deg,#9fc4ec,#2d6db5)" role="img" aria-label="Document and chart icon"></div>
            <div><h4>Services Title</h4><p>Sed sed tellus ut lorem vestibulum gravida. Vivamus elementum ut felis sodales. Curabitur rutrum.</p><a class="more" href="#">LEARN MORE &#9656;</a></div>
          </div>
          <div class="service">
            <div class="service-icon" style="background:linear-gradient(135deg,#b8e08a,#4f9a2a)" role="img" aria-label="Green check badge icon"></div>
            <div><h4>Services Title</h4><p>Sed sed tellus ut lorem vestibulum gravida. Vivamus elementum ut felis sodales. Curabitur rutrum.</p><a class="more" href="#">LEARN MORE &#9656;</a></div>
          </div>
        </div>
      </section>
    </div>
    <aside class="side-col">
      <h2 class="section-title">In the News</h2>
      <div class="news-item">
        <h4>Fusce ultricies orci</h4>
        <p>Morbi magna tempus tincidunt a, mattis non, imperdiet vitae tellus. Sed odio est, auctor ac, sollicitudin in, consequat vitae.</p>
        <time>Tuesday, 19 June 2012 14:08</time>
      </div>
      <div class="news-item">
        <h4>Etiam est nunc</h4>
        <p>Morbi magna tempus tincidunt a, mattis non, imperdiet vitae tellus. Sed odio est, auctor ac, sollicitudin in, consequat vitae.</p>
        <time>Saturday, 09 June 2012 11:20</time>
      </div>
    </aside>
  </div>
</main>

<footer class="site-footer">
  <div class="wrap">
    <div class="footer-cols">
      <div class="footer-col"><h5>Company</h5><ul><li>Home</li><li>About Us</li><li>FAQ</li><li>Services Provide</li><li>Training Program</li></ul></div>
      <div class="footer-col"><h5>Sublinks</h5><ul><li>Tour</li><li>Features</li><li>Pricing</li><li>Sign Up</li><li>Member Login</li></ul></div>
      <div class="footer-col"><h5>Sublinks</h5><ul><li>Careers</li><li>Support</li><li>Privacy Policy</li><li>Terms of Use</li><li>Sitemap</li></ul></div>
      <div class="footer-col"><h5>Support</h5><ul><li>Contact</li><li>Support</li><li>Privacy Policy</li><li>Terms of Use</li><li>Sitemap</li></ul></div>
      <div class="newsletter">
        <h5>Newsletters Subscribe</h5>
        <p>Please sign up now for latest news &amp; offers</p>
        <form><span class="field"></span><span class="btn">SUBSCRIBE</span></form>
        <div class="social"><i></i><i></i><i></i><i></i><i></i></div>
      </div>
    </div>
  </div>
  <div class="copyright"><div class="wrap">Copyright © 2013 Talvoro. All rights reserved.</div></div>
</footer>
</body>
</html>
```